Kestrel Facilities Business Card Design

We would now like to design business cards with the new Kestrel Facilities logo

Target Market(s)

Professional

Industry/Entity Type

Professional services

Contact Information for Business Card

Employee name, title, phone number, email address, corporate office address and logo.

Font styles to use
Sans Serif

Colors
0054AA
0677BA
7BADD7
CADEEF
E8F1F8

Requirements
Must have
• My logo
Should not have
• any other pictures or images besides my logo

```html
<!DOCTYPE html>
<html lang="en">
<head>
<meta charset="utf-8">
<title>Kestrel Facilities Business Card</title>
<link rel="stylesheet" href="https://fonts.googleapis.com/css2?family=Montserrat:wght@500;700&family=Josefin+Sans:wght@400&display=swap">
<style>
  :root {
    --brand-deep: #0054AA;
    --brand-mid: #0677BA;
    --brand-soft: #7BADD7;
    --brand-pale: #CADEEF;
    --brand-mist: #E8F1F8;
    --ink: #1f2a33;
    --page: #eef0f2;
  }
  * { box-sizing: border-box; margin: 0; padding: 0; }
  html, body {
    width: 1200px; height: 969px; overflow: hidden;
    background: var(--page);
  }
  .card {
    position: absolute; left: 100px; top: 200px;
    width: 1000px; height: 570px;
    border-radius: 30px;
    background: var(--brand-mist);
    border: 1px solid var(--brand-pale);
  }
  .brand {
    position: absolute; left: 82px; top: 205px;
    display: flex; align-items: center; gap: 22px;
  }
  .brand-square {
    width: 130px; height: 130px;
    background: var(--brand-mid);
  }
  .brand-name {
    font-family: "Montserrat", sans-serif; font-weight: 700;
    font-size: 44px; line-height: 1.12; color: var(--brand-mid);
    letter-spacing: 1px; text-transform: uppercase;
  }
  .divider {
    position: absolute; left: 522px; top: 146px;
    width: 3px; height: 296px; background: var(--brand-mid);
  }
  .details { position: absolute; left: 568px; top: 140px; }
  .person-name {
    font-family: "Montserrat", sans-serif; font-weight: 700;
    font-size: 34px; color: var(--brand-mid); letter-spacing: -0.3px;
  }
  .person-title {
    font-family: "Montserrat", sans-serif; font-weight: 500;
    font-size: 25px; color: var(--ink); margin-top: 2px;
  }
  .address {
    font-family: "Josefin Sans", sans-serif; font-size: 25px;
    color: var(--ink); line-height: 37px; margin-top: 24px;
  }
  .contacts { list-style: none; margin-top: 14px; }
  .contact {
    display: flex; align-items: center; gap: 12px;
    font-family: "Montserrat", sans-serif; font-weight: 500;
    font-size: 25px; color: var(--ink); height: 38px;
  }
  .contact svg { width: 22px; height: 22px; fill: var(--brand-deep); flex: none; }
</style>
</head>
<body>
  <div class="card">
    <div class="brand">
      <div class="brand-square"></div>
      <div class="brand-name">Kestrel<br>Facilities</div>
    </div>
    <div class="divider"></div>
    <div class="details">
      <h1 class="person-name">WANJIRU ATIENO</h1>
      <p class="person-title">Co-Founder</p>
      <p class="address">P.O Box 4418-00200<br>Nairobi, Kenya</p>
      <ul class="contacts">
        <li class="contact">
          <svg viewBox="0 0 24 24" aria-hidden="true"><path d="M2 8c0-3 4-5 10-5s10 2 10 5v2h-5V8c-1-.8-3-1.2-5-1.2S8 7.2 7 8v2H2z"/><path d="M6 11h12l2 9H4z"/></svg>
          +254-700-41526
        </li>
        <li class="contact">
          <svg viewBox="0 0 24 24" aria-hidden="true"><path d="M2 5h20v2l-10 6L2 7z"/><path d="M2 9.5l10 6 10-6V19H2z"/></svg>
          hello@kestrelfacilities.co
        </li>
        <li class="contact">
          <svg viewBox="0 0 24 24" aria-hidden="true"><circle cx="12" cy="12" r="10"/><path d="M8 6c2 1 3 3 1 4s-2 3 0 4 1 4 0 5" stroke="#E8F1F8" stroke-width="1.6" fill="none"/><path d="M15 5c-1 2 1 3 3 3M14 14c2-1 4 0 4 2" stroke="#E8F1F8" stroke-width="1.6" fill="none"/></svg>
          www.kestrelfacilities.co
        </li>
      </ul>
    </div>
  </div>
</body>
</html>
```